New Fun, Positive, energised looking Business Card Needed for High Achiever Coach

I am looking for a two sided full colour business card. I am self employed and have recently re branded my 1-2-1 work re-vitalising high achievers. My target client base for these cards is therefore high achievers - usually aged 40 -55, they are often entrepreneurs, CEO or work in banking and finance and 2/3 are male. I work with them on 90 day or 6 month coaching programs to help them live their success in a healthier, more sustainable and fulfiiled way. They pay for this privately so though they are corporate types the cards need not look 'corporate'. I want to portray the idea of transformation, vitality and re-connecting.
You can get a feel for the look I like on my new website: morvenlisk.co.uk
I want to use this logo with strapline (Re-Vitalising High Achievers) (I purchased off Logoharbor) and font/ colours (the turquoise and green).
Details to include on the card:
www.morvenlisk.co.uk
+44 7915 302618
morven@morvenlisk.co.uk
skype: morvenlisk
I'd also like to include:
Do you struggle to switch off? Want to be healthier and feel fitter? Want closer relationships? More clarity over the direction you are headed? I can help you do these things using integrated mind-body techniques. Visit morvenlisk.co.uk TODAY to apply for a FREE Breakthrough session.
BUT if that is too much text for a card I am open to advice/ammendments.
Updates
Thanks for your design - I am considering them. PLease change the wording to :

```html
<!DOCTYPE html>
<html lang="en">
<head>
<meta charset="utf-8">
<title>Morven Lisk – Business Card</title>
<link rel="stylesheet" href="https://fonts.googleapis.com/css2?family=Open+Sans:wght@400;600;700&display=swap">
<style>
  :root {
    --backdrop: #e4e4e4;
    --turquoise: #12a8c8;
    --teal-deep: #0d9cc2;
    --sky: #8fd3e8;
    --green: #6cbf4f;
    --orange: #f39a2b;
    --ink: #4a4a4a;
    --white: #ffffff;
  }
  * { margin: 0; padding: 0; box-sizing: border-box; }
  html, body {
    width: 1200px; height: 693px; overflow: hidden;
    background: var(--backdrop);
    font-family: "Open Sans", Arial, sans-serif;
  }
  .canvas { position: relative; width: 1200px; height: 693px; }
  .card {
    position: absolute; width: 460px; height: 268px; overflow: hidden;
  }

  /* Back side */
  .card-back {
    left: 96px; top: 198px;
    background: var(--turquoise); color: var(--white);
    text-align: center;
  }
  .back-brand {
    position: absolute; top: 56px; left: 0; right: 0;
    font-size: 17px; font-weight: 700; letter-spacing: .3px;
  }
  .back-pitch {
    position: absolute; top: 108px; left: 26px; right: 26px;
    font-size: 12.5px; line-height: 16px;
  }
  .back-cta {
    position: absolute; top: 198px; left: 0; right: 0;
    font-size: 12px; word-spacing: 2px; white-space: nowrap;
  }
  .back-cta strong { font-weight: 700; }

  /* Front side */
  .card-front { left: 646px; top: 196px; background: var(--white); }
  .front-brand {
    position: absolute; left: 32px; top: 58px;
    display: flex; align-items: center; gap: 10px;
  }
  .brand-dot {
    width: 30px; height: 30px; border-radius: 50%; background: var(--green);
  }
  .brand-name {
    font-size: 24px; font-weight: 700; color: var(--teal-deep);
  }
  .holder {
    position: absolute; right: 40px; top: 104px; text-align: right;
  }
  .holder-name { font-size: 13px; color: var(--teal-deep); line-height: 17px; }
  .holder-role { font-size: 10.5px; color: var(--green); line-height: 14px; }
  .contacts {
    position: absolute; left: 72px; top: 158px; list-style: none;
    font-size: 11px; color: var(--ink);
  }
  .contacts li { display: flex; align-items: center; gap: 6px; height: 16px; }
  .contacts svg { width: 9px; height: 9px; flex: none; }
  .website {
    position: absolute; right: 40px; top: 193px;
    font-size: 12px; font-weight: 700; color: var(--teal-deep);
  }
  .base-band {
    position: absolute; left: 0; right: 0; bottom: 0; height: 40px;
    background: linear-gradient(180deg, var(--sky) 0%, var(--turquoise) 70%);
  }
</style>
</head>
<body>
<main class="canvas">

  <section class="card card-back" aria-label="Card back">
    <div class="back-brand">Morven Lisk</div>
    <p class="back-pitch">
      Do you struggle to switch off?<br>
      Want to be healthier and feel fitter?<br>
      Want closer relationships? More clarity over the direction you are headed?Let me help you reach your goals using integrated mind-body techniques.
    </p>
    <p class="back-cta">Visit <strong>morvenlisk.co.uk</strong> TODAY to apply for a <strong>FREE</strong> Breakthrough session.</p>
  </section>

  <section class="card card-front" aria-label="Card front">
    <div class="front-brand">
      <span class="brand-dot"></span>
      <span class="brand-name">Morven Lisk</span>
    </div>

    <div class="holder">
      <div class="holder-name">Morven Lisk</div>
      <div class="holder-role">President/Revitalising Coach</div>
    </div>

    <ul class="contacts">
      <li>
        <svg viewBox="0 0 10 10"><path d="M2 0.5 L3.6 2.6 L2.8 3.6 C3.4 5 4.8 6.5 6.3 7.2 L7.4 6.3 L9.5 8 L8.3 9.5 C4.5 9.2 0.8 5.5 0.5 1.7 Z" fill="var(--orange)"/></svg>
        +44 7915 302618
      </li>
      <li>
        <svg viewBox="0 0 10 10"><circle cx="5" cy="5" r="4.6" fill="var(--orange)"/></svg>
        morvenlisk
      </li>
      <li>
        <svg viewBox="0 0 10 10"><rect x="0.5" y="2" width="9" height="6.5" fill="var(--orange)"/><path d="M0.8 2.3 L5 5.6 L9.2 2.3" fill="none" stroke="#fff" stroke-width="0.9"/></svg>
        morven@morvenlisk.co.uk
      </li>
    </ul>

    <div class="website">www.morvenlisk.co.uk</div>

    <div class="base-band" role="img" aria-label="Decorative wave band in turquoise, orange and green"></div>
  </section>

</main>
</body>
</html>
```